Aunt Wilma's Ember-Kissed Husk Shack Concession Trailer Logo Wraps

Looking to put my design concept into a final production-ready format for vinyl-based logo "wrap" on the exterior of a 7x12 black concession trailer selling farm-fresh corn on the cob slathered in flavor flamboyance, corn in a cup, corn over crushed snacks (Crunvels, Zaplins, Puffnars, etc.) served in the bags, fire-roasted street corn (Mexican elotes), corn grits, corn chowder, cornbread, corndogs. I have my fonts and colors and a flame graphic I've roughly edited/reworked attempting to make it work and need a design pro to bring it all together for me. The approximate size of the graphics on the four sides of the trailer will be: the serving window when closed (48"L x 24"H); front (48"x48"); full right side (11'x5'); door (6'x2') and possibly the left side next to door (3'x5'). Pictures uploaded.
Target Market(s)
Food truck festivals, private catering gigs, fairs, farm markets, concerts, etc.
Font styles to use
Other font styles liked:
- flame fetish, Algerian
Requirements
Must have
- My color scheme as depicted in uploaded files, flame fetish font uploaded (will consider similar fonts), flame/fire artwork, bright bold colors that pop against a black background
Nice to have
- straight line of flames on each side of the "fire-roasted" text, flowing from the first and last letter

```html
<!DOCTYPE html>
<html lang="en">
<head>
<meta charset="utf-8">
<title>Aunt Wilma's Ember-Kissed Husk Shack</title>
<link rel="stylesheet" href="https://fonts.googleapis.com/css2?family=Yesteryear&family=Kaushan+Script&family=Rye&display=swap">
<style>
  :root {
    --ink: #000000;
    --cyan: #08ece4;
    --cyan-edge: #2b39f0;
    --flame-deep: #b8200a;
    --flame-mid: #f2661a;
    --flame-hot: #ffc23a;
    --glow: #ff7a12;
    --corn-yellow: #f6df1c;
    --tag-gold: #f2b61c;
  }
  html, body {
    margin: 0;
    padding: 0;
    width: 1200px;
    height: 600px;
    overflow: hidden;
    background: var(--ink);
  }
  .wrap-panel {
    display: block;
    width: 1200px;
    height: 600px;
  }
  .brand-name {
    font-family: "Yesteryear", cursive;
    font-size: 170px;
    fill: var(--cyan);
    stroke: var(--cyan-edge);
    stroke-width: 3px;
    paint-order: stroke fill;
  }
  .roast-line {
    font-family: "Kaushan Script", cursive;
    font-size: 92px;
    fill: #0b0b0b;
    filter: drop-shadow(0 0 4px var(--glow)) drop-shadow(0 0 9px var(--glow));
  }
  .product-title {
    font-family: "Rye", serif;
    font-size: 132px;
    fill: var(--corn-yellow);
  }
  .product-title-shadow {
    font-family: "Rye", serif;
    font-size: 132px;
    fill: none;
    stroke: var(--corn-yellow);
    stroke-width: 1.6px;
  }
  .tagline {
    font-family: "Kaushan Script", cursive;
    font-size: 38px;
    fill: var(--tag-gold);
  }
</style>
</head>
<body>
<svg class="wrap-panel" viewBox="0 0 1200 600" xmlns="http://www.w3.org/2000/svg">
  <defs>
    <linearGradient id="flameRise" x1="0" y1="1" x2="0" y2="0">
      <stop offset="0" stop-color="var(--flame-deep)" stop-opacity="0.95"/>
      <stop offset="0.35" stop-color="var(--flame-mid)" stop-opacity="0.9"/>
      <stop offset="0.7" stop-color="var(--flame-hot)" stop-opacity="0.35"/>
      <stop offset="1" stop-color="var(--flame-deep)" stop-opacity="0"/>
    </linearGradient>
    <linearGradient id="flameSpread" x1="0" y1="0" x2="1" y2="0">
      <stop offset="0" stop-color="#fff" stop-opacity="1"/>
      <stop offset="0.22" stop-color="#fff" stop-opacity="0.55"/>
      <stop offset="0.5" stop-color="#fff" stop-opacity="0.35"/>
      <stop offset="0.78" stop-color="#fff" stop-opacity="0.55"/>
      <stop offset="1" stop-color="#fff" stop-opacity="1"/>
    </linearGradient>
    <mask id="flameMask">
      <rect x="0" y="120" width="1200" height="240" fill="url(#flameSpread)"/>
    </mask>
    <linearGradient id="smokeBand" x1="0" y1="0" x2="0" y2="1">
      <stop offset="0" stop-color="#5c5246" stop-opacity="0.7"/>
      <stop offset="0.6" stop-color="#3a332b" stop-opacity="0.45"/>
      <stop offset="1" stop-color="#000" stop-opacity="0"/>
    </linearGradient>
  </defs>

  <rect class="backdrop" x="0" y="0" width="1200" height="600" fill="var(--ink)"/>

  <g class="flame-artwork" role="img" aria-label="Band of realistic fire flames rising across the panel, tallest at the left and right edges">
    <rect x="0" y="120" width="1200" height="240" fill="url(#flameRise)" mask="url(#flameMask)"/>
  </g>

  <rect class="smoke-band" x="0" y="346" width="1200" height="130" fill="url(#smokeBand)"/>

  <text class="brand-name" x="600" y="218" text-anchor="middle" textLength="1070" lengthAdjust="spacingAndGlyphs">Aunt Wilma's</text>

  <text class="roast-line" x="600" y="330" text-anchor="middle" textLength="470" lengthAdjust="spacingAndGlyphs">ember-kissed</text>

  <text class="product-title-shadow" x="604" y="486" text-anchor="middle" textLength="1060" lengthAdjust="spacingAndGlyphs">HUSK SHACK</text>
  <text class="product-title" x="600" y="480" text-anchor="middle" textLength="1060" lengthAdjust="spacingAndGlyphs">HUSK SHACK</text>

  <text class="tagline" x="600" y="545" text-anchor="middle" textLength="760" lengthAdjust="spacingAndGlyphs">Sweet cobs dripping with bold and smoky goodness!</text>
</svg>
</body>
</html>
```